Brightmoor Talent company

We require a website for job recruitment company called "Brightmoor Talent"
Our company is specialising in recruitment of skilled labour from Sri Lanka into Australian market.
We would like to include a job advertising plugin where jobs can be listed and applied for .
COPYWRITING MUST BE INCLUDED !

Industry/Entity Type

Recruitment

Coding

Coded - Design and coding required

Number of Pages Required

5+ page

Colors

Designer to choose colors to be used in the design.

```html
<!DOCTYPE html>
<html lang="en">
<head>
<meta charset="utf-8">
<title>Brightmoor Talent</title>
<link href="https://fonts.googleapis.com/css2?family=Noto+Serif:wght@700&family=Roboto:wght@400;500&family=Montserrat:wght@500;600&display=swap" rel="stylesheet">
<style>
:root{
  --blue:#0b4ea2;
  --blue-dark:#083d82;
  --blue-light:#2a68b8;
  --ink:#1c1c1c;
  --muted:#555;
  --white:#fff;
  --line:#c9c9c9;
  --pale:#eef1f6;
}
*{box-sizing:border-box;margin:0;padding:0}
html,body{width:1200px;height:4195px;overflow:hidden;background:var(--white)}
body{font-family:"Roboto",sans-serif;color:var(--ink)}
.page{position:relative;width:1200px;height:4195px;overflow:hidden}
.abs{position:absolute}
.serif{font-family:"Noto Serif",serif;font-weight:700}

/* header */
.brand{position:absolute;font-family:"Noto Serif",serif;font-weight:700;color:var(--blue);line-height:1}
.brand .top{display:block;font-size:38px;letter-spacing:-.5px}
.brand .sub{display:block;font-size:22px;letter-spacing:10px;margin-top:4px;padding-left:38px}
.header-btn{position:absolute;top:13px;height:36px;font:500 12px "Roboto",sans-serif;display:flex;align-items:center;justify-content:center;border-radius:3px;text-transform:uppercase}
.btn-outline{border:1.5px solid var(--ink);color:var(--ink)}
.btn-solid{background:var(--blue);color:var(--white)}
.nav{position:absolute;top:66px;right:173px;display:flex;gap:27px;font:500 13.5px "Roboto",sans-serif;color:var(--ink)}

/* hero */
.hero-photo{position:absolute;left:0;top:101px;width:1200px;height:720px;background:linear-gradient(120deg,#7b8796 0%,#c8ced6 35%,#e9ebee 60%,#cfd3d8 100%)}
.search-circle{position:absolute;left:764px;top:212px;width:472px;height:472px;border-radius:50%;background:var(--white)}
.search-title{position:absolute;left:780px;width:340px;text-align:center;color:var(--blue)}
.field{position:absolute;left:793px;width:345px;height:38px;border:1.5px solid var(--line);border-radius:3px;background:var(--white);font-size:10.5px;color:#777;padding:0 10px;display:flex;align-items:center;justify-content:space-between}
.search-btn{position:absolute;left:899px;top:575px;width:135px;height:39px;background:var(--blue);color:var(--white);font:700 14px "Noto Serif",serif;display:flex;align-items:center;justify-content:center;border-radius:3px}

.section-title{position:absolute;left:0;width:1200px;text-align:center;font-family:"Noto Serif",serif;font-weight:700;text-transform:uppercase}

/* industries */
.industry{position:absolute;top:985px;width:180px;text-align:center;color:var(--white)}
.industry svg{display:block;margin:0 auto 14px}
.industry .name{font:500 17px "Roboto",sans-serif;letter-spacing:.3px}
.industry .count{font-size:13.5px;margin-top:8px}

/* jobs */
.job-card{position:absolute;left:171px;width:856px;height:138px;background:var(--white);box-shadow:0 2px 8px rgba(0,0,0,.18);border-radius:3px}
.job-card.raised{box-shadow:0 4px 14px rgba(0,0,0,.4)}
.company-box{position:absolute;top:7px;width:118px;height:124px;border:1.5px solid #555;border-radius:4px;display:flex;align-items:center;justify-content:center;gap:5px;font:500 14px "Roboto",sans-serif;color:var(--ink)}
.company-box i{display:block;width:12px;height:12px;background:var(--ink)}
.job-title{position:absolute;top:22px;font:500 16.5px "Roboto",sans-serif;letter-spacing:.5px}
.job-meta{position:absolute;top:55px;font-size:14px;display:flex;gap:18px;align-items:center}
.job-meta span{display:flex;align-items:center;gap:6px}
.job-desc{position:absolute;top:82px;width:540px;font-size:11.5px;color:var(--muted);line-height:17px}
.view-btn{position:absolute;top:48px;width:103px;height:40px;border:1.5px solid var(--blue);color:var(--blue);font:700 13px "Noto Serif",serif;display:flex;align-items:center;justify-content:center;border-radius:3px}
.view-btn.solid{background:var(--blue);color:var(--white)}
.left .company-box{left:7px}.left .job-title,.left .job-meta,.left .job-desc{left:138px}.left .view-btn{right:20px}
.right .company-box{right:7px}.right .job-title,.right .job-meta,.right .job-desc{right:138px;text-align:right}.right .job-meta{justify-content:flex-end}.right .view-btn{left:20px}

/* why */
.why-right{position:absolute;left:0;top:2071px;width:1200px;height:524px;background:linear-gradient(90deg,#e4e8ef,#f6f7f9 60%,#e9ecf1)}
.acc{position:absolute;left:680px;width:347px;height:42px;border:1.5px solid #555;border-radius:3px;background:var(--white);font:500 14px "Roboto",sans-serif;display:flex;align-items:center;justify-content:space-between;padding:0 12px}
.acc b{font-weight:400;font-size:24px;line-height:1}
.acc-text{position:absolute;left:680px;top:2278px;width:350px;font-size:11.5px;line-height:21px;color:#444}

/* clients */
.quote-card{position:absolute;top:2800px;width:422px;height:332px;background:var(--white);box-shadow:0 2px 10px rgba(0,0,0,.2);text-align:center}
.avatar{position:absolute;left:157px;top:44px;width:108px;height:108px;border-radius:50%;border:2px solid #333;background:linear-gradient(160deg,#d9cfc6,#7d6e63)}
.quote-text{position:absolute;left:16px;top:192px;width:390px;font-size:12.5px;line-height:19.5px;color:#444}
.quote-name{position:absolute;left:0;top:284px;width:100%;font:700 15px "Noto Serif",serif;color:var(--blue)}

/* blog */
.blog-card{position:absolute;top:3318px;width:276px;height:394px;background:var(--white);text-align:center}
.blog-img{height:195px}
.blog-card h3{margin-top:20px;font:700 20px "Noto Serif",serif;color:var(--ink)}
.blog-card p{margin:11px 10px 0;font-size:12.5px;line-height:19.5px;color:#555}
.read-btn{display:inline-flex;margin-top:13px;width:102px;height:38px;background:var(--blue);color:var(--white);font:700 13px "Noto Serif",serif;align-items:center;justify-content:center;border-radius:3px}

/* footer */
.foot-col{position:absolute;top:3872px;font-family:"Montserrat",sans-serif}
.foot-col h4{font:700 20px "Noto Serif",serif;color:var(--ink);margin-bottom:14px}
.post{font-size:12px;font-weight:600;line-height:16px;width:200px}
.post small{display:block;font-weight:500;font-size:11.5px;color:#444;margin:4px 0 11px}
.links a{display:block;font-size:12px;font-weight:600;color:var(--ink);text-decoration:none;line-height:24.5px}
.contact-row{display:flex;gap:12px;font-size:12px;font-weight:600;line-height:17px;margin-bottom:17px}
.contact-row svg{flex:none}
.copyright{position:absolute;left:0;top:4135px;width:1200px;height:60px;background:var(--blue);color:var(--white);font:500 13.5px "Montserrat",sans-serif;display:flex;align-items:center;justify-content:center}
</style>
</head>
<body>
<div class="page">

  <!-- header -->
  <div class="brand" style="left:171px;top:16px"><span class="top">Brightmoor</span><span class="sub">Talent</span></div>
  <div class="header-btn btn-outline" style="left:812px;width:111px">Broese Jobs</div>
  <div class="header-btn btn-solid" style="left:933px;width:94px">Post a Job</div>
  <nav class="nav"><span>HOME</span><span>ABOUT</span><span>BLOG</span><span>SERVICES</span><span>BLOG</span><span>CONTACT</span></nav>

  <!-- hero -->
  <div class="hero-photo" role="img" aria-label="Photo of two businessmen shaking hands in a bright office meeting room"></div>
  <svg class="abs" style="left:0;top:600px" width="1200" height="605" viewBox="0 600 1200 605">
    <path d="M0,720 C250,780 520,860 820,790 C980,750 1100,690 1200,640 L1200,1205 L0,1205Z" fill="var(--blue-light)"/>
    <path d="M0,700 C260,760 540,830 820,775 C990,740 1100,670 1200,620 L1200,1205 L0,1205Z" fill="var(--blue)" opacity=".0"/>
    <path d="M0,700 C240,770 500,820 800,800 C960,790 1100,720 1200,680 L1200,1205 L0,1205Z" fill="var(--blue)"/>
  </svg>
  <div class="search-circle"></div>
  <div class="search-title serif" style="top:278px;font-size:35px">FIND THE MOST</div>
  <div class="search-title serif" style="top:319px;font-size:28px">EXCITING JOBS</div>
  <div class="search-title" style="top:364px;font:500 14.5px 'Roboto',sans-serif;color:var(--ink)">Find your dream job here...</div>
  <div class="field" style="top:410px">Job, title, keywords</div>
  <div class="field" style="top:464px">Anywhere <span style="color:#222;font-size:9px">▼</span></div>
  <div class="field" style="top:519px">Part Time</div>
  <div class="search-btn">SEARCH JOB</div>

  <!-- industries -->
  <div class="section-title" style="top:893px;font-size:27px;color:var(--white)">Jobs by Industry</div>
  <div class="industry" style="left:141px">
    <svg width="70" height="70" viewBox="0 0 70 70" fill="none" stroke="#fff" stroke-width="2.5"><rect x="8" y="6" width="40" height="54" rx="3"/><rect x="28" y="28" width="34" height="38" rx="3"/><rect x="33" y="33" width="24" height="8"/><path d="M34 47h4M42 47h4M50 47h4M34 54h4M42 54h4M50 54h4M34 60h4M42 60h4M50 60h4M14 26v-8M20 26v-12M26 26v-6M20 2v6"/></svg>
    <div class="name">ACCOUNTING</div><div class="count">10 Postitions</div></div>
  <div class="industry" style="left:328px">
    <svg width="70" height="70" viewBox="0 0 70 70" fill="none" stroke="#fff" stroke-width="2.5"><rect x="14" y="4" width="32" height="60" rx="4"/><path d="M14 54h32M26 59h8M20 14h16M20 20h12M20 26h14"/><path d="M30 38l16-8v22l-16-8z"/><path d="M52 34l8-4M52 41h9M52 48l8 4"/></svg>
    <div class="name">DIGITAL</div><div class="count">2 Postitions</div></div>
  <div class="industry" style="left:524px">
    <svg width="70" height="70" viewBox="0 0 70 70" fill="none" stroke="#fff" stroke-width="2.5"><path d="M6 22L35 6l29 16z"/><path d="M8 26h54M8 58h54M4 64h62"/><rect x="14" y="30" width="7" height="24"/><rect x="27" y="30" width="7" height="24"/><rect x="40" y="30" width="7" height="24"/><rect x="53" y="30" width="3" height="24"/></svg>
    <div class="name">BANKING</div><div class="count">11 Postitions</div></div>
  <div class="industry" style="left:711px">
    <svg width="70" height="70" viewBox="0 0 70 70" fill="none" stroke="#fff" stroke-width="2.5"><circle cx="35" cy="14" r="8"/><circle cx="35" cy="14" r="3"/><path d="M14 44l6-14h30l6 14"/><rect x="8" y="44" width="54" height="14" rx="3"/><path d="M12 58v8h10v-8M48 58v8h10v-8"/><circle cx="18" cy="51" r="3"/><circle cx="52" cy="51" r="3"/><path d="M28 51h14"/></svg>
    <div class="name">AUTOMOTIVE</div><div class="count">20 Postitions</div></div>
  <div class="industry" style="left:893px">
    <svg width="70" height="70" viewBox="0 0 70 70" fill="none" stroke="#fff" stroke-width="2.5"><rect x="4" y="12" width="62" height="40" rx="3"/><path d="M4 44h62M35 52v10M22 64h26"/><path d="M56 4L34 30l-4 8 8-4L60 8z"/><path d="M22 38c4 0 8-2 8-6"/></svg>
    <div class="name">DESIGN</div><div class="count">15 Postitions</div></div>

  <!-- recent jobs -->
  <div class="section-title" style="top:1272px;font-size:35px;color:var(--blue)">Recent Jobs</div>

  <div class="job-card left" style="top:1368px">
    <div class="company-box"><i></i>Northvale</div>
    <div class="job-title">SALES AND MARKETING COORDINATOR</div>
    <div class="job-meta"><span>&#9678; Australia</span><span>&#8853; Full Time</span></div>
    <div class="job-desc">Duis aute irure dolor in reprehenderit in voluptate velit esse cillum dolore eu fugiat nulla pariatur. Excepteur sint occaecat cupidatat non proident.</div>
    <div class="view-btn">VIEW MORE</div>
  </div>
  <div class="job-card right raised" style="top:1525px">
    <div class="company-box"><i></i>KESTREL</div>
    <div class="job-title">CAR TRANSPORTER</div>
    <div class="job-meta"><span>Full Time &#8853;</span><span>Australia &#9678;</span></div>
    <div class="job-desc">Duis aute irure dolor in reprehenderit in voluptate velit esse cillum dolore eu fugiat nulla pariatur. Excepteur sint occaecat cupidatat non proident.</div>
    <div class="view-btn solid">VIEW MORE</div>
  </div>
  <div class="job-card left" style="top:1690px">
    <div class="company-box"><i></i>Northvale</div>
    <div class="job-title">ELECTRONICS TECHNICIAN</div>
    <div class="job-meta"><span>&#9678; Australia</span><span>&#8853; Full Time</span></div>
    <div class="job-desc">Duis aute irure dolor in reprehenderit in voluptate velit esse cillum dolore eu fugiat nulla pariatur. Excepteur sint occaecat cupidatat non proident.</div>
    <div class="view-btn">VIEW MORE</div>
  </div>
  <div class="job-card right" style="top:1848px">
    <div class="company-box"><i></i>KESTREL</div>
    <div class="job-title">ENGINEERING TECHNICIAN</div>
    <div class="job-meta"><span>Full Time &#8853;</span><span>Australia &#9678;</span></div>
    <div class="job-desc">Duis aute irure dolor in reprehenderit in voluptate velit esse cillum dolore eu fugiat nulla pariatur. Excepteur sint occaecat cupidatat non proident.</div>
    <div class="view-btn">VIEW MORE</div>
  </div>

  <!-- why choose us -->
  <div class="why-right" role="img" aria-label="Faded photo of a bright office background"></div>
  <svg class="abs" style="left:0;top:2071px" width="560" height="524" role="img" aria-label="Blue tinted photo of a businessman reading a tablet">
    <defs><linearGradient id="whyTint" x1="0" y1="0" x2="1" y2="1"><stop offset="0" stop-color="#1d5aa6"/><stop offset="1" stop-color="#0e4590"/></linearGradient></defs>
    <path d="M0 0H540L520 524H0Z" fill="url(#whyTint)"/>
  </svg>
  <div class="abs serif" style="left:680px;top:2140px;font-size:35px;color:var(--blue)">WHY CHOOSE US</div>
  <div class="acc" style="top:2217px">Nemo enim ipsam voluptatem? <b>&#8722;</b></div>
  <div class="acc-text">Aliquam sapien est, mollis id mattis id, scelerisque sed dolor. Proin accumsan erat sem, id porta risus dignissim ac. Vestibulum nec sapien in lacus ornare nec nec justo.</div>
  <div class="acc" style="top:2352px">Enim ad minima veniam? <b>+</b></div>
  <div class="acc" style="top:2412px">Sed ut perspiciatis unde omnis? <b>+</b></div>
  <div class="acc" style="top:2473px">Quis autem vel eum iure reprehenderit? <b>+</b></div>

  <!-- clients -->
  <div class="section-title" style="top:2677px;font-size:35px;color:var(--blue)">Words from our Clients</div>
  <svg class="abs" style="left:0;top:2900px" width="1200" height="903" viewBox="0 2900 1200 903">
    <path d="M0,2930 Q600,3070 1200,2930 L1200,3803 L0,3803Z" fill="var(--blue)"/>
  </svg>
  <div class="quote-card" style="left:171px">
    <div class="avatar" role="img" aria-label="Client portrait"></div>
    <div class="quote-text">Nemo enim ipsam voluptatem quia voluptas sit aspernatur aut odit aut fugit, sed quia consequuntur magni dolores eos qui ratio ne voluptatem sequi nesciunt. Neque porro quisquam est, qui dolorem ipsum quia dolor sit amet, consectetur</div>
    <div class="quote-name">- Daniel Fenwick</div>
  </div>
  <div class="quote-card" style="left:606px">
    <div class="avatar" role="img" aria-label="Client portrait" style="background:linear-gradient(160deg,#cfd0d2,#5c5f64)"></div>
    <div class="quote-text">Nemo enim ipsam voluptatem quia voluptas sit aspernatur aut odit aut fugit, sed quia consequuntur magni dolores eos qui ratio ne voluptatem sequi nesciunt. Neque porro quisquam est, qui dolorem ipsum quia dolor sit amet, consectetur</div>
    <div class="quote-name">- Marcus Halloway</div>
  </div>

  <!-- blog -->
  <div class="section-title" style="top:3213px;font-size:35px;color:var(--white)">Latest Blog</div>
  <div class="blog-card" style="left:173px">
    <div class="blog-img" role="img" aria-label="Photo of colleagues shaking hands at a meeting table" style="background:linear-gradient(135deg,#5a5f66,#c9c4bd)"></div>
    <h3>NEMO ENIM IPSAM</h3>
    <p>Sed ut perspiciatis unde omnis iste natus error sit voluptatem accusantium dolorem que laudantium, totam rem aperiam,</p>
    <span class="read-btn">READ MORE</span>
  </div>
  <div class="blog-card" style="left:462px">
    <div class="blog-img" role="img" aria-label="Photo of a business meeting with a laptop" style="background:linear-gradient(135deg,#3d3f44,#b9b7b4)"></div>
    <h3>NEMO ENIM IPSAM</h3>
    <p>Sed ut perspiciatis unde omnis iste natus error sit voluptatem accusantium dolorem que laudantium, totam rem aperiam,</p>
    <span class="read-btn">READ MORE</span>
  </div>
  <div class="blog-card" style="left:751px">
    <div class="blog-img" role="img" aria-label="Photo of a cheering business team" style="background:linear-gradient(135deg,#d8d9db,#6b6f75)"></div>
    <h3>NEMO ENIM IPSAM</h3>
    <p>Sed ut perspiciatis unde omnis iste natus error sit voluptatem accusantium dolorem que laudantium, totam rem aperiam,</p>
    <span class="read-btn">READ MORE</span>
  </div>

  <!-- footer -->
  <div class="brand" style="left:171px;top:3938px"><span class="top" style="font-size:44px">Brightmoor</span><span class="sub" style="font-size:25px;padding-left:50px">Talent</span></div>
  <div class="foot-col" style="left:428px">
    <h4>RECENT POSTS</h4>
    <div class="post">Nemo enim ipsam voluptatem quia voluptas<small>June 15, 2019</small></div>
    <div class="post">Nemo enim ipsam voluptatem quia voluptas<small>June 15, 2019</small></div>
    <div class="post">Nemo enim ipsam voluptatem quia voluptas<small>June 15, 2019</small></div>
  </div>
  <div class="foot-col links" style="left:661px">
    <h4>QUICK LINKS</h4>
    <a>Home</a><a>About</a><a>Blog</a><a>Services</a><a>Jobs</a><a>Contact</a>
  </div>
  <div class="foot-col" style="left:830px;width:200px">
    <h4>CONTACT US</h4>
    <div class="contact-row"><svg width="28" height="28" viewBox="0 0 28 28" fill="none" stroke="var(--blue)" stroke-width="1.8"><circle cx="14" cy="14" r="13"/><path d="M14 21s-5-5-5-9a5 5 0 0 1 10 0c0 4-5 9-5 9z"/><circle cx="14" cy="12" r="1.8"/></svg><span>48 Harbour Lane, Westmere, VIC 3351</span></div>
    <div class="contact-row"><svg width="28" height="28" viewBox="0 0 28 28" fill="none" stroke="var(--blue)" stroke-width="1.8"><circle cx="14" cy="14" r="13"/><path d="M10 8l3 0 1 3-2 1.5a8 8 0 0 0 3.5 3.5L17 14l3 1v3c-6 1-11-4-10-10z"/></svg><span>(03) 5550 1824<br>(03) 5550 1937</span></div>
    <div class="contact-row"><svg width="28" height="28" viewBox="0 0 28 28" fill="none" stroke="var(--blue)" stroke-width="1.8"><circle cx="14" cy="14" r="13"/><rect x="8" y="9" width="12" height="10" rx="1"/><path d="M8 10l6 5 6-5"/></svg><span>Mail:<br>info@brightmoortalent.com</span></div>
  </div>
  <div class="copyright">Copyrights @ 2022 Brightmoor Talent.</div>
</div>
</body>
</html>
```